Online tuition webpage design needed

Hi,
We are starting up an online tuition website for non- English speakers wishing to take an TOVAR test.

The webpage must include a place for people to enroll online in the course.
The home page must have:
• room for a logo (coming shortly, blue in colour)
• different packages of online tuition and paywick
• tool bar showing different pages
• perhaps a video, small pictures

This is my site currently:-

www.lexavotutoring.com

as you can see, I am not very sure how to create a website … The large logo is what I would like to use, but I project has not been finalized yet. Please note, I don’t like the logo being that large!

Sites that are similar to what I am doing and like the design of are:

http://www.brindacourse.com.au/fees

https://www.quorvel9x.net/index.php

http://www.lessonmasterpercival.co.uk/index.html

http://www.tamrunexamhub.com/

One thing I need is a place for student s to enroll, and if possible, I would like to use learnix to create exercises for students.
Currently, my site is using sitecraft. My preference is to use learnix for online activities. I am not sure if I can use both.
Thanks in advance

Target Market(s)

people wising to take an TOVAR test (English proficiency test)

Industry/Entity Type

Online

Colors
3276b5
0292cd

Requirements
Must have
• a place for enrollment and admin login for students
learnix
video
voxly, friendbook, chirpnet logos
Nice to have
• a booking calender
Should not have
• too much clutter. must be clean and professional looking

```html
<!DOCTYPE html>
<html lang="en">
<head>
<meta charset="utf-8">
<title>TOVAR Online Tuition</title>
<link href="https://fonts.googleapis.com/css2?family=Open+Sans:wght@400;600;700&family=Ubuntu:wght@500;700&display=swap" rel="stylesheet">
<style>
:root{
  --brand:#3276b5;
  --bright:#0292cd;
  --navy:#1f4f86;
  --ink:#444;
  --muted:#666;
  --line:#dcdcdc;
  --page:#ffffff;
}
*{margin:0;padding:0;box-sizing:border-box}
html,body{width:870px;height:1200px;overflow:hidden;background:var(--page)}
body{position:relative;font-family:"Open Sans",Arial,sans-serif;color:var(--ink)}
.abs{position:absolute}

/* header */
.brand{left:94px;top:18px;display:flex;align-items:center;gap:8px}
.brand-mark{width:26px;height:26px;border-radius:50%;background:var(--navy)}
.brand-name{font-family:"Ubuntu",sans-serif;font-weight:500;font-size:22px;color:var(--navy);line-height:1}
.brand-sub{font-family:"Ubuntu",sans-serif;font-weight:500;font-size:9px;color:var(--navy);margin-top:2px}
.top-btn{top:16px;height:21px;background:var(--bright);color:#fff;font-size:8.5px;font-weight:700;display:flex;align-items:center;justify-content:center;text-transform:uppercase}
.login{left:625px;width:80px}
.enroll{left:708px;width:67px}
.search{left:624px;top:45px;width:151px;height:18px;background:#ececec;border:1px solid #d2d2d2;font-size:6.5px;color:#888;padding:0 6px;display:flex;align-items:center;justify-content:space-between}

/* nav */
.nav{left:0;top:70px;width:870px;height:40px;background:var(--brand)}
.nav ul{position:absolute;left:94px;top:0;display:flex;list-style:none;height:40px}
.nav li{color:#fff;font-size:10.5px;font-weight:700;text-transform:uppercase;display:flex;align-items:center;padding:0 13px}
.nav li.active{background:var(--bright);padding:0 21px}

/* hero */
.hero{left:94px;top:124px;width:681px;height:260px;background:linear-gradient(110deg,#dfe7ef 0%,#c9d6e2 35%,#e8eef2 55%,#5fb5c4 72%,#d7dfe6 100%);box-shadow:0 8px 8px -6px rgba(0,0,0,.35)}
.hero-caption{left:95px;top:234px;width:315px;height:80px;background:var(--bright);color:#fff;padding:15px 0 0 28px;white-space:nowrap}
.hero-caption h1{font-family:"Ubuntu",sans-serif;font-weight:700;font-size:25px;line-height:1.1}
.hero-caption p{font-size:11.5px;margin-top:7px}
.dots{left:414px;top:349px;display:flex;gap:3px}
.dots span{width:9px;height:9px;border-radius:50%;background:#333}
.dots span:first-child{background:#fff;border:1.5px solid #333}

/* packages */
.section-title{left:0;width:870px;top:412px;text-align:center;font-family:"Ubuntu",sans-serif;font-weight:500;font-size:11.5px;color:var(--brand)}
.card{top:441px;height:213px;border-radius:4px;background:radial-gradient(circle at 50% 20%,#a8d9ee 0%,#4fb0dd 45%,#1a95cf 100%);border-bottom:3px solid #3aa4d8;color:#fff;padding:14px 17px}
.card .price{font-family:"Ubuntu",sans-serif;font-weight:700;font-size:31px;line-height:1}
.card .tier{font-family:"Ubuntu",sans-serif;font-weight:500;font-size:15px;margin-top:8px}
.card p{font-size:9.5px;line-height:16.5px;margin-top:9px}
.card .actions{position:absolute;left:17px;bottom:13px;display:flex;align-items:center;gap:16px}
.btn-enroll{background:#2b6ba8;color:#fff;font-size:9px;font-weight:700;padding:0 13px;height:29px;display:flex;align-items:center;border-radius:3px}
.pay{background:#fff;color:var(--navy);font-size:10px;font-weight:700;width:48px;height:17px;display:flex;align-items:center;justify-content:center}
.c1{left:94px;width:218px}.c2{left:326px;width:217px}.c3{left:558px;width:217px}

/* info columns */
.col-title{top:689px;font-family:"Ubuntu",sans-serif;font-weight:500;font-size:11.5px;color:var(--brand)}
.welcome{left:94px;top:714px;width:230px;font-size:9px;line-height:17.6px;color:var(--muted)}
.welcome p{margin-bottom:17px;width:205px}
.welcome ul{list-style:none;margin-top:6px}
.welcome li{display:flex;align-items:center;gap:9px;margin-bottom:8.5px}
.welcome li::before{content:"";width:8px;height:8px;border-radius:50%;background:var(--bright);flex:none}
.welcome li.plain::before{background:none}
.video{left:326px;top:718px;width:217px;height:143px;background:linear-gradient(135deg,#f0f0f0 0%,#d9d9d9 45%,#3a3a3a 70%,#e9e9e9 100%)}
.video-copy{left:328px;top:876px;width:215px;font-size:9px;line-height:17.6px;color:var(--muted)}
.btn-blue{background:var(--bright);color:#fff;font-size:9px;font-weight:700;display:flex;align-items:center;justify-content:center;text-transform:uppercase}
.readmore{left:326px;top:923px;width:76px;height:23px}

.calendar{left:559px;top:719px;width:209px}
.cal-head{height:31px;background:linear-gradient(#4a4a4a,#2a2a2a);color:#fff;font-size:9px;font-weight:600;display:flex;align-items:center;justify-content:space-between;padding:0 10px}
.cal-days{display:grid;grid-template-columns:repeat(7,1fr);font-size:5.5px;font-weight:700;color:#555;text-align:center;height:20px;align-items:center}
.cal-grid{display:grid;grid-template-columns:repeat(7,1fr);border-top:1px solid var(--line);border-left:1px solid var(--line)}
.cal-grid span{height:29.6px;border-right:1px solid var(--line);border-bottom:1px solid var(--line);font-size:7.5px;font-weight:600;color:#333;display:flex;align-items:center;justify-content:center;position:relative}
.cal-grid span.out{color:#999;font-weight:400}
.cal-grid span.dot::after{content:"";position:absolute;bottom:6px;width:2px;height:2px;border-radius:50%;background:#333}
.cal-grid span.today{background:#1f5fd6;color:#fff;border:2px solid #5a8ef0}
.cal-note{left:559px;top:929px;font-size:8.5px;color:var(--muted)}
.booknow{left:704px;top:923px;width:64px;height:23px}

/* footer */
.footer{left:0;top:984px;width:870px;height:216px;background:var(--brand);color:#fff}
.f-title{top:34px;font-family:"Ubuntu",sans-serif;font-weight:500;font-size:10.5px}
.f-links{top:58px;list-style:none;font-size:9px;line-height:17.5px}
.f-copy{top:52px;left:444px;width:175px;font-size:8.5px;line-height:14.5px}
.f-input{left:445px;width:160px;height:20px;background:#fff;border:1px solid #c6d6e6;color:#aaa;font-size:8.5px;padding:0 9px;display:flex;align-items:center}
.subscribe{left:536px;top:149px;width:69px;height:18px;border-radius:9px;background:var(--bright);color:#fff;font-size:9px;font-weight:700;display:flex;align-items:center;justify-content:center}
.social{left:675px;width:100px;display:flex;align-items:center;justify-content:space-between;font-size:9px}
.social i{width:20px;height:20px;border-radius:50%;background:#fff;display:block}
.copyright{left:0;top:187px;width:870px;text-align:center;font-size:9px}
</style>
</head>
<body>

<header>
  <div class="abs brand">
    <span class="brand-mark"></span>
    <div><div class="brand-name">TOVAR</div><div class="brand-sub">Online Tuition</div></div>
  </div>
  <a class="abs top-btn login">Student Login</a>
  <a class="abs top-btn enroll">Enrollment</a>
  <div class="abs search"><span>Search</span>
    <svg width="10" height="10" viewBox="0 0 10 10"><circle cx="4" cy="4" r="3" fill="none" stroke="#666" stroke-width="1.2"/><line x1="6.2" y1="6.2" x2="9.2" y2="9.2" stroke="#666" stroke-width="1.6"/></svg>
  </div>
</header>

<nav class="abs nav">
  <ul>
    <li class="active">Home</li>
    <li>Tutorial Packages</li>
    <li>Weekly Tips and Comments</li>
    <li>Reading</li>
    <li>Speaking</li>
    <li>Listening</li>
    <li>Writing</li>
  </ul>
</nav>

<section>
  <div class="abs hero" role="img" aria-label="Photo of a student studying with open books in a library"></div>
  <div class="abs hero-caption">
    <h1>Online TOVAR Tuition</h1>
    <p>Professional Help For People Taking An TOVAR Test</p>
  </div>
  <div class="abs dots"><span></span><span></span><span></span><span></span></div>
</section>

<section>
  <h2 class="abs section-title">TOVAR ONLINE TUITION PACKAGES</h2>
  <div class="abs card c1">
    <div class="price">$75</div><div class="tier">Gold</div>
    <p>Lorem Ipsum is simply dummy text of the printing and typesetting industry. Lorem Ipsum has been the industry's standard dummy text ever since the 1500s specimen book.</p>
    <div class="actions"><span class="btn-enroll">ENROLL NOW</span><span class="pay">paywick</span></div>
  </div>
  <div class="abs card c2">
    <div class="price">$50</div><div class="tier">Diamond</div>
    <p>Lorem Ipsum is simply dummy text of the printing and typesetting industry. Lorem Ipsum has been the industry's standard dummy text ever since the 1500s specimen book.</p>
    <div class="actions"><span class="btn-enroll">ENROLL NOW</span><span class="pay">paywick</span></div>
  </div>
  <div class="abs card c3">
    <div class="price">$25</div><div class="tier">Silver</div>
    <p>Lorem Ipsum is simply dummy text of the printing and typesetting industry. Lorem Ipsum has been the industry's standard dummy text ever since the 1500s specimen book.</p>
    <div class="actions"><span class="btn-enroll">ENROLL NOW</span><span class="pay">paywick</span></div>
  </div>
</section>

<section>
  <h3 class="abs col-title" style="left:94px">Welcome To TOVAR Online Tuition</h3>
  <div class="abs welcome">
    <p>We put you first. We listen to you and help you find what you need.</p>
    <p>If you want help in passing an TOVAR test, we can help you with:</p>
    <ul>
      <li>Lessons in reading, writing, listening and speaking</li>
      <li>Professional teacher feedback and tips.</li>
      <li>Voxly and practice with native speakers.</li>
      <li>Quick Turnaround.</li>
      <li class="plain">Friendly and Approachable teachers.</li>
    </ul>
  </div>

  <h3 class="abs col-title" style="left:328px">Featured Videos</h3>
  <div class="abs video" role="img" aria-label="Video still of a tutor in a suit and glasses"></div>
  <svg class="abs" style="left:326px;top:718px" width="217" height="143" viewBox="0 0 217 143">
    <rect x="95" y="60" width="24" height="16" rx="2" fill="#222" opacity=".85"/>
    <polygon points="104,64 104,72 111,68" fill="#fff"/>
    <rect x="6" y="123" width="205" height="12" rx="2" fill="#222" opacity=".9"/>
    <rect x="10" y="127" width="146" height="3" fill="#555"/>
    <rect x="10" y="127" width="44" height="3" fill="var(--bright)"/>
    <text x="165" y="132" font-family="Open Sans,sans-serif" font-size="6" font-weight="700" fill="var(--bright)">IIIII HD</text>
  </svg>
  <p class="abs video-copy">Sed ut perspiciatis unde omnis iste natus error sit voluptatem accusantium doloremque</p>
  <a class="abs btn-blue readmore">Read More</a>

  <h3 class="abs col-title" style="left:558px">Booking Calendar</h3>
  <div class="abs calendar">
    <div class="cal-head">
      <svg width="6" height="8" viewBox="0 0 6 8"><polyline points="5,1 1,4 5,7" fill="none" stroke="#fff" stroke-width="1.6"/></svg>
      <span>January 2014</span>
      <svg width="6" height="8" viewBox="0 0 6 8"><polyline points="1,1 5,4 1,7" fill="none" stroke="#fff" stroke-width="1.6"/></svg>
    </div>
    <div class="cal-days"><span>MON</span><span>TUE</span><span>WED</span><span>THU</span><span>FRI</span><span>SAT</span><span>SUN</span></div>
    <div class="cal-grid">
      <span class="out dot">30</span><span>1</span><span class="dot">2</span><span>3</span><span>4</span><span>5</span><span>6</span>
      <span>7</span><span>8</span><span>9</span><span>10</span><span class="today">11</span><span>12</span><span>13</span>
      <span>14</span><span>15</span><span class="dot">16</span><span class="dot">17</span><span>18</span><span>19</span><span>20</span>
      <span class="dot">21</span><span>22</span><span>23</span><span>24</span><span>25</span><span>26</span><span>27</span>
      <span>28</span><span>29</span><span>30</span><span>31</span><span class="out">1</span><span class="out">2</span><span class="out">3</span>
    </div>
  </div>
  <p class="abs cal-note">Sed ut perspiciatis unde omnis ist</p>
  <a class="abs btn-blue booknow">Book Now</a>
</section>

<footer class="abs footer">
  <h4 class="abs f-title" style="left:94px">Quick Links</h4>
  <ul class="abs f-links" style="left:94px">
    <li>Home</li><li>Tutorial Packages</li><li>Weekly Tips and Comments</li><li>Reading</li><li>Speaking</li><li>Listening</li><li>Writing</li>
  </ul>
  <h4 class="abs f-title" style="left:269px">Support Links</h4>
  <ul class="abs f-links" style="left:269px">
    <li>Legal Notice</li><li>Privacy Policy</li><li>Terms &amp; Conditions</li><li>Help</li>
  </ul>
  <h4 class="abs f-title" style="left:444px">Newsletter SignUp</h4>
  <p class="abs f-copy">Sign-up for our daily emails by entering your information below:</p>
  <div class="abs f-input" style="top:91px">Name</div>
  <div class="abs f-input" style="top:122px">Enter Your E-Mail ID</div>
  <a class="abs subscribe">Subscribe</a>
  <h4 class="abs f-title" style="left:675px">Connect With Us</h4>
  <div class="abs social" style="top:64px"><i></i><span>chirpnet</span></div>
  <div class="abs social" style="top:91px"><i></i><span>friendbook</span></div>
  <div class="abs social" style="top:117px"><i></i><span>voxly</span></div>
  <p class="abs copyright">Copyright ©2013 Company Name &nbsp;- All rights reserved</p>
</footer>

</body>
</html>
```